Copperbend Blazeworks Website Design

I am looking for a website design ( Home page and inner template page ) in a .psd format. The home page needs to have a large hero image what will function as a "slider", and have some highlight graphical areas/links to the following links "Public & Municipal Events", "Corporate Events", "Special Events". The main navigation needs to have the following nav links "gallery", "home", "about", "services" and "contact". Unfortunately the client does not have any nice hi-rez images ( this is a company that specializes is large fireworks displays ) so please use stock photography sample images from snapvaultpics since we have an account there an can purchase the photos if our client wants to use them. Our current full time graphic artist has been with us for a long time so we are looking at artflockhub as a way to add a fresh approach to design and possibly find someone we can work with regularly. Here is a few designs that in the way we display them for our clients for approval. As you can see there are a couple that don't have their own images so they are utilizing the before mentioned snapvaultpics samples. On the plus side we did manage to get their logo in a .ai format. We have our team for handling the conversion from design to html.

http://reedfoxbuildstudio.com/dev/

```html
<!DOCTYPE html>
<html lang="en">
<head>
<meta charset="utf-8">
<title>Copperbend Blazeworks</title>
<link href="https://fonts.googleapis.com/css2?family=Roboto:wght@400;500;700&family=Tinos&display=swap" rel="stylesheet">
<style>
:root{
  --bg:#050505;
  --ink:#ffffff;
  --accent:#3fa2dc;
  --muted:#d8d8d8;
  --footer:#0b0f19;
  --frame:#e6e6e6;
}
*{margin:0;padding:0;box-sizing:border-box}
html,body{width:1200px;height:3024px;overflow:hidden}
body{background:var(--bg);color:var(--ink);font-family:"Roboto",Arial,sans-serif;position:relative}
.serif{font-family:"Tinos","Times New Roman",serif;font-weight:400}

/* hero */
.hero{position:absolute;left:0;top:0;width:1200px;height:735px;
  background:
   radial-gradient(ellipse 220px 170px at 780px 270px,rgba(235,70,80,.75),transparent 70%),
   radial-gradient(ellipse 170px 120px at 470px 580px,rgba(230,60,80,.55),transparent 70%),
   radial-gradient(ellipse 150px 110px at 160px 610px,rgba(230,70,90,.5),transparent 70%),
   radial-gradient(ellipse 240px 120px at 820px 500px,rgba(220,220,230,.35),transparent 70%),
   radial-gradient(ellipse 400px 120px at 350px 720px,rgba(40,120,220,.55),transparent 70%),
   linear-gradient(180deg,#050507 0%,#0a0b14 55%,#121a30 100%)}
.topbar{position:absolute;right:103px;top:18px;font-size:17px;font-weight:500;display:flex;align-items:center;gap:12px;white-space:nowrap}
.social-dot{width:11px;height:11px;border-radius:50%;background:var(--ink);display:inline-block}
.nav{position:absolute;top:62px;right:102px;display:flex;font-size:16px;font-weight:500;white-space:nowrap}
.nav a{color:var(--ink);text-decoration:none}
.nav .sep{margin:0 46px}
.brand{position:absolute;display:flex;align-items:center;gap:9px;white-space:nowrap}
.brand .mark{width:20px;height:20px;border-radius:50%;background:var(--accent);flex:none}
.brand-top{left:97px;top:100px;font-size:24px}
.hero-title{position:absolute;left:97px;top:292px;font-size:61px;line-height:61px;white-space:nowrap}
.btn{position:absolute;background:var(--accent);color:#fff;font-weight:700;font-size:16px;display:flex;align-items:center;justify-content:center;border-radius:3px}
.arrow{position:absolute;top:342px}
.dots{position:absolute;left:560px;top:655px;display:flex;gap:8px}
.dots span{width:14px;height:14px;border:2px solid #fff;border-radius:50%}
.dots span.on{background:#fff}

/* section titles */
.section-title{position:absolute;left:0;width:1200px;text-align:center;font-size:45px;line-height:50px}
.rule{position:absolute;height:2px;width:110px;background:var(--accent)}

.card{position:absolute;width:318px;height:364px;border:2px solid var(--frame)}
.card-label{position:absolute;width:318px;text-align:center;font-size:23px}

.about-art{position:absolute;left:158px;top:1420px;width:341px;height:429px;
  background:radial-gradient(ellipse at 45% 35%,rgba(110,160,200,.55),rgba(60,100,140,.2) 55%,transparent 75%)}
.about-title{position:absolute;left:585px;top:1473px;font-size:45px;line-height:50px}
.about-text{position:absolute;left:585px;top:1563px;width:470px;font-size:14.5px;line-height:26.4px;letter-spacing:-.3px}

.tile{position:absolute;border:2px solid var(--frame)}

/* footer */
.footer{position:absolute;left:0;top:2466px;width:1200px;height:558px;
  background:radial-gradient(ellipse 300px 200px at 600px 130px,rgba(80,40,50,.35),transparent 70%),
  radial-gradient(ellipse 260px 180px at 900px 400px,rgba(50,40,60,.3),transparent 70%),var(--footer)}
.news-title{position:absolute;top:2536px;left:0;width:1200px;text-align:center;font-size:35px;line-height:40px}
.news-sub{position:absolute;top:2580px;left:0;width:1200px;text-align:center;font-size:15px}
.news-form{position:absolute;left:295px;top:2617px;width:609px;height:48px;background:#fff;border:2px solid #fff}
.news-form .ph{position:absolute;left:34px;top:13px;color:#888;font-size:15px}
.news-form .box{position:absolute;left:13px;top:17px;width:12px;height:10px;background:#999;border-radius:2px}
.news-form .submit{position:absolute;right:0;top:0;width:142px;height:44px;background:var(--accent);color:#fff;font-weight:700;font-size:16px;display:flex;align-items:center;justify-content:center;gap:8px}
.hr{position:absolute;left:103px;width:994px;height:1px;background:#3a3d47}
.brand-foot{left:100px;top:2866px;font-size:23px}
.col-title{position:absolute;font-size:17px;font-weight:700}
.col-link{position:absolute;color:var(--ink);text-decoration:none;font-size:15px;white-space:nowrap}
.contact-line{position:absolute;left:822px;font-size:15px;line-height:19px;white-space:nowrap}
.contact-icon{position:absolute;left:795px}
.copy{position:absolute;top:2979px;left:0;width:1200px;text-align:center;font-size:15px}
.fsocial{position:absolute;top:2926px;width:16px;height:16px;border-radius:50%;background:#fff}
</style>
</head>
<body>

<header class="hero" role="img" aria-label="Photograph of red and white fireworks bursting over a city skyline at night"></header>
<div class="topbar">
  <svg width="14" height="14" viewBox="0 0 24 24"><path fill="#fff" d="M6.6 10.8a15 15 0 0 0 6.6 6.6l2.2-2.2c.3-.3.7-.4 1-.2 1.1.4 2.3.6 3.6.6.6 0 1 .4 1 1V20c0 .6-.4 1-1 1C10.6 21 3 13.4 3 4c0-.6.4-1 1-1h3.5c.6 0 1 .4 1 1 0 1.2.2 2.4.6 3.6.1.3 0 .7-.2 1z"/></svg>
  <span>What do I need for my event?</span><span>|</span><span>(555) 204-7781</span><span>|</span>
  <span class="social-dot"></span><span class="social-dot"></span><span class="social-dot"></span>
</div>
<nav class="nav">
  <a href="#">HOME</a><span class="sep">|</span><a href="#">GALLERY</a><span class="sep">|</span><a href="#">ABOUT</a><span class="sep">|</span><a href="#">SERVICES</a><span class="sep">|</span><a href="#">CONTACT</a>
</nav>
<div class="brand brand-top serif"><span class="mark"></span>Copperbend Blazeworks</div>
<h1 class="hero-title serif">We'll Help You Make<br>the Magic Happen</h1>
<div class="btn" style="left:99px;top:438px;width:156px;height:42px">GET STARTED</div>
<svg class="arrow" style="left:68px" width="18" height="36" viewBox="0 0 18 36"><polyline points="16,2 2,18 16,34" fill="none" stroke="#fff" stroke-width="1.6"/></svg>
<svg class="arrow" style="left:1113px" width="18" height="36" viewBox="0 0 18 36"><polyline points="2,2 16,18 2,34" fill="none" stroke="#fff" stroke-width="1.6"/></svg>
<div class="dots"><span class="on"></span><span></span><span></span><span></span></div>

<h2 class="section-title serif" style="top:820px">OUR SERVICES</h2>
<div class="rule" style="left:545px;top:884px"></div>

<div class="card" style="left:100px;top:916px;background:linear-gradient(180deg,#3b4a6e,#6d6a46 55%,#1f2740)" role="img" aria-label="Fireworks over a golden lift bridge"></div>
<div class="card" style="left:441px;top:916px;background:radial-gradient(ellipse at 40% 25%,#c0308a,#4a0f30 50%,#1a0508)" role="img" aria-label="Pink and red fireworks above a harbour"></div>
<div class="card" style="left:782px;top:916px;background:radial-gradient(ellipse at 55% 35%,#8a97a8,#2b3644 55%,#141a22)" role="img" aria-label="White fireworks reflected on a river at night"></div>
<div class="card-label serif" style="left:100px;top:1295px">Public &amp; Municipal Events</div>
<div class="card-label serif" style="left:441px;top:1295px">Corporate Events</div>
<div class="card-label serif" style="left:782px;top:1295px">Special Events</div>

<div class="about-art" role="img" aria-label="Blue firework burst illustration with small stars"></div>
<h2 class="about-title serif">ABOUT US</h2>
<div class="rule" style="left:585px;top:1537px"></div>
<p class="about-text">Lorem ipsum dolor sit amet, consectetur adipiscing elit, tempor incididunt ut labore et dolore magna al Risus commodo viverra maecenas accumsan lacus vel facilisis. Lorem ipsum dolor stetur adipt, sed do eiusmod tempor incididunt ut labore et dolore magna aliqua. suspendisse ultrices gravida. Risus commodo viverra maecenas facilissit amet, consectetur adipiscing elit, tempor incididunt ut labore et</p>
<div class="btn" style="left:585px;top:1742px;width:156px;height:43px">LEARN MORE</div>

<h2 class="section-title serif" style="top:1896px">OUR GALLERY</h2>
<div class="rule" style="left:545px;top:1960px"></div>

<div class="tile" style="left:100px;top:1992px;width:241px;height:184px;background:radial-gradient(ellipse at 50% 40%,#b8806a,#3a2230 60%,#0c0a10)" role="img" aria-label="Multicoloured fireworks"></div>
<div class="tile" style="left:100px;top:2189px;width:241px;height:184px;background:linear-gradient(180deg,#2a1f44,#8a6ab8 45%,#c07a40 75%,#0c0a10)" role="img" aria-label="Purple and orange fountain fireworks"></div>
<div class="tile" style="left:353px;top:1992px;width:241px;height:381px;background:linear-gradient(180deg,#6b4a30,#3a2a22 45%,#16120e)" role="img" aria-label="Golden fireworks above trees and a crowd"></div>
<div class="tile" style="left:606px;top:1992px;width:241px;height:184px;background:radial-gradient(ellipse at 50% 35%,#b37ab8,#3a2e5a 60%,#141428)" role="img" aria-label="Pink fireworks over a city"></div>
<div class="tile" style="left:606px;top:2189px;width:241px;height:184px;background:radial-gradient(ellipse at 50% 40%,#4a9a8a,#2a2a5a 60%,#0e0e1c)" role="img" aria-label="Green and blue fireworks"></div>
<div class="tile" style="left:859px;top:1992px;width:241px;height:381px;background:radial-gradient(ellipse at 45% 40%,#b0502a,#4a140c 55%,#0a0404)" role="img" aria-label="Orange and red fireworks"></div>

<footer class="footer" role="img" aria-label="Faint fireworks backdrop"></footer>
<h2 class="news-title serif">SUBSCRIBE OUR NEWSLETTER</h2>
<div class="news-sub">Sed ut perspiciatis unde omnis iste natus error sit voluptatem accusantium</div>
<div class="news-form">
  <span class="box"></span><span class="ph">Your Email Address..</span>
  <div class="submit"><svg width="15" height="15" viewBox="0 0 24 24"><path fill="#fff" d="M2 11 22 2l-5 20-5-7-6 5 2-7z"/></svg>SUBMIT</div>
</div>
<div class="hr" style="top:2694px"></div>

<div class="brand brand-foot serif"><span class="mark" style="width:16px;height:16px"></span>Copperbend Blazeworks</div>
<span class="fsocial" style="left:125px"></span><span class="fsocial" style="left:175px"></span><span class="fsocial" style="left:226px"></span><span class="fsocial" style="left:276px"></span>

<h4 class="col-title" style="left:391px;top:2738px">PAGES</h4>
<a class="col-link" style="left:392px;top:2780px">Home</a>
<a class="col-link" style="left:392px;top:2808px">Gallery</a>
<a class="col-link" style="left:396px;top:2836px">About</a>
<a class="col-link" style="left:392px;top:2864px">Services</a>
<a class="col-link" style="left:392px;top:2892px">Contact</a>
<h4 class="col-title" style="left:549px;top:2738px">SERVICES</h4>
<a class="col-link" style="left:550px;top:2780px">Public &amp; Municipal Events</a>
<a class="col-link" style="left:550px;top:2808px">Corporate Events</a>
<a class="col-link" style="left:550px;top:2836px">Special Events</a>
<h4 class="col-title" style="left:794px;top:2738px">CONTACT</h4>

<svg class="contact-icon" style="top:2782px" width="14" height="20" viewBox="0 0 14 20"><path fill="#fff" d="M7 0a7 7 0 0 0-7 7c0 5 7 13 7 13s7-8 7-13a7 7 0 0 0-7-7zm0 10a3 3 0 1 1 0-6 3 3 0 0 1 0 6z"/></svg>
<div class="contact-line" style="top:2780px">4810 Ember Lane Harlow Falls<br>55872</div>
<svg class="contact-icon" style="top:2832px" width="17" height="17" viewBox="0 0 24 24"><path fill="#fff" d="M6.6 10.8a15 15 0 0 0 6.6 6.6l2.2-2.2c.3-.3.7-.4 1-.2 1.1.4 2.3.6 3.6.6.6 0 1 .4 1 1V20c0 .6-.4 1-1 1C10.6 21 3 13.4 3 4c0-.6.4-1 1-1h3.5c.6 0 1 .4 1 1 0 1.2.2 2.4.6 3.6.1.3 0 .7-.2 1z"/></svg>
<div class="contact-line" style="top:2834px;font-size:13px">Phone : 555 318 6402</div>
<svg class="contact-icon" style="top:2866px" width="20" height="15" viewBox="0 0 20 15"><rect width="20" height="15" rx="1" fill="#fff"/><polyline points="1,1 10,8 19,1" fill="none" stroke="#0b0f19" stroke-width="1.6"/></svg>
<div class="contact-line" style="top:2864px">Email : info@copperbendblazeworks.com</div>

<div class="hr" style="top:2958px"></div>
<div class="copy">© 2020 Copperbend Blazeworks . All Rights Reserved.</div>

</body>
</html>
```